Verdanith Website Concept

We would like a one page website. Please refer to the attached files for more information.

Please reference file attachment version 1.1.

```html
<!DOCTYPE html>
<html lang="en">
<head>
<meta charset="utf-8">
<title>Verdanith – Financial Security Service</title>
<link href="https://fonts.googleapis.com/css2?family=Mulish:wght@400;500;600;700&family=Open+Sans:wght@400;600&display=swap" rel="stylesheet">
<style>
:root{
  --navy:#233066;
  --navy-top:#52608f;
  --brand-blue:#1b3fa0;
  --link-blue:#1c3aa8;
  --cyan:#1aa6d6;
  --cyan-light:#4cc6ec;
  --hero-sub:#4a62c4;
  --text:#444;
  --text-soft:#666;
  --muted:#888;
  --line:#d6d6d6;
  --nav-bg:#f3f3f3;
  --footer-bg:#f2f2f2;
  --orange:#ff7a00;
  --orange-light:#ff9a1e;
  --white:#fff;
}
*{box-sizing:border-box;margin:0;padding:0}
html,body{width:902px;height:1200px;overflow:hidden;background:var(--white)}
body{position:relative;font-family:"Open Sans",Arial,sans-serif;color:var(--text)}
.abs{position:absolute}

.site-header{position:absolute;left:0;top:0;width:902px;height:84px;background:var(--white)}
.brand{position:absolute;left:88px;top:30px;display:flex;align-items:center;gap:8px}
.brand-mark{width:30px;height:30px;border-radius:50%;background:var(--brand-blue)}
.brand-name{font-family:"Mulish",sans-serif;font-weight:600;font-size:22px;color:var(--navy);letter-spacing:.5px}
.support{position:absolute;right:84px;top:31px;text-align:right;font-family:"Mulish",sans-serif}
.support-label{font-size:12px;color:var(--muted)}
.support-phone{display:flex;align-items:center;gap:4px;font-size:18px;font-weight:600;color:var(--brand-blue)}

.main-nav{position:absolute;left:0;top:84px;width:902px;height:42px;background:linear-gradient(#fafafa,var(--nav-bg));border-top:1px solid #e2e2e2}
.main-nav ul{list-style:none;display:flex;position:absolute;left:88px;top:0;height:42px}
.main-nav li{font-family:"Mulish",sans-serif;font-size:14px;color:#333;height:42px;line-height:41px;padding:0 16px;border-right:1px solid #cfcfcf}
.main-nav li:last-child{border-right:none}

.hero-band{position:absolute;left:0;top:126px;width:902px;height:286px;background:linear-gradient(var(--navy-top),var(--navy))}
.hero{position:absolute;left:74px;top:147px;width:754px;height:323px;background:linear-gradient(90deg,#eef0f3,#fafafa 45%,#e4e4e4);overflow:hidden;box-shadow:0 1px 3px rgba(0,0,0,.2)}
.hero-photo{position:absolute;right:0;top:0;width:380px;height:323px;background:linear-gradient(90deg,rgba(240,240,240,0),#6b6b6b 30%,#3c3c3c 60%,#555)}
.hero-title{position:absolute;left:52px;top:106px;font-family:"Mulish",sans-serif;font-weight:700;font-size:24px;color:var(--cyan)}
.hero-sub{position:absolute;left:52px;top:142px;font-family:"Mulish",sans-serif;font-size:15px;color:var(--hero-sub)}
.hero-text{position:absolute;left:52px;top:166px;font-size:10px;line-height:16px;color:#555}
.hero-dots{position:absolute;left:52px;top:206px;display:flex;gap:3px}
.hero-dots span{width:10px;height:10px;border-radius:50%;background:#8e96ad}

.service{position:absolute;top:510px;width:165px}
.service-img{width:165px;height:75px}
.service h3{font-family:"Mulish",sans-serif;font-weight:500;font-size:13px;line-height:20px;color:var(--link-blue);margin-top:7px}
.service p{font-size:9px;line-height:15px;color:var(--text-soft);margin-top:3px}

.divider{position:absolute;left:72px;top:689px;width:509px;height:1px;background:var(--line)}
.welcome{position:absolute;left:76px;top:715px;width:490px}
.welcome h1{font-family:"Mulish",sans-serif;font-weight:400;font-size:21px;color:#333;margin-bottom:8px}
.welcome p{font-size:9.6px;line-height:16.3px;color:var(--text-soft);margin-bottom:9px}
.welcome p.lead{color:#444}
.welcome p.gap{margin-top:24px}

.consult{position:absolute;left:604px;top:506px;width:224px;height:528px;border:1px solid #dcdcdc;border-radius:3px;background:var(--white)}
.consult-head{height:43px;background:linear-gradient(var(--cyan-light),var(--cyan));border-radius:3px 3px 0 0;color:var(--white);font-family:"Mulish",sans-serif;font-size:15px;font-weight:500;padding:12px 20px}
.field{position:absolute;left:18px;width:190px;height:25px;border:1px solid #d8d8d8;border-radius:2px;font-size:9.5px;color:#777;padding:5px 10px}
.field.message{height:60px}
.submit{position:absolute;left:19px;top:485px;width:88px;height:28px;background:linear-gradient(var(--orange-light),var(--orange));border-radius:2px;color:var(--white);font-family:"Mulish",sans-serif;font-weight:600;font-size:13px;text-align:center;line-height:28px}

.site-footer{position:absolute;left:0;top:1101px;width:902px;height:99px;background:var(--footer-bg);border-top:1px solid #e4e4e4}
.footer-nav{position:absolute;left:79px;top:24px;font-size:11.5px;color:#555}
.footer-nav span.sep{margin:0 6px;color:#777}
.copyright{position:absolute;left:79px;top:54px;font-size:9.5px;color:#666}
.social{position:absolute;left:760px;top:27px;display:flex;gap:6px}
.social span{width:15px;height:15px;border-radius:1px}
</style>
</head>
<body>

<header class="site-header">
  <div class="brand"><span class="brand-mark"></span><span class="brand-name">Verdanith</span></div>
  <div class="support">
    <div class="support-label">24/7 Support</div>
    <div class="support-phone">
      <svg width="14" height="14" viewBox="0 0 24 24"><path fill="#c8c8c8" d="M6.6 10.8c1.4 2.8 3.8 5.1 6.6 6.6l2.2-2.2c.3-.3.7-.4 1-.2 1.1.4 2.3.6 3.6.6.6 0 1 .4 1 1V20c0 .6-.4 1-1 1C10.6 21 3 13.4 3 4c0-.6.4-1 1-1h3.5c.6 0 1 .4 1 1 0 1.3.2 2.5.6 3.6.1.3 0 .7-.2 1z"/></svg>
      555.014.2290
    </div>
  </div>
</header>

<nav class="main-nav">
  <ul>
    <li>Home</li><li>About Us</li><li>Our Services</li><li>Security</li><li>Testimonials</li><li>Team</li><li>Support</li><li>Contact Us</li>
  </ul>
</nav>

<div class="hero-band"></div>
<section class="hero">
  <div class="hero-photo" role="img" aria-label="Businessman in a grey suit touching a glowing cloud padlock symbol"></div>
  <h2 class="hero-title">FINANCIAL SECURITY SERVICE</h2>
  <p class="hero-sub">Mauris vel lacus vitae felis vestibulum volutpat</p>
  <p class="hero-text">Phasellus felis dolor scelerisque a tempus eget lobortis id libero<br>Aliquam nec erat at purus cursus interdum Vestibul</p>
  <div class="hero-dots"><span></span><span></span><span></span><span></span></div>
</section>

<article class="service" style="left:74px">
  <div class="service-img" role="img" aria-label="Digital fingerprint scan interface" style="background:linear-gradient(135deg,#1c2a7a,#3f5ed6 50%,#b23a8a)"></div>
  <h3>Threat Assessment</h3>
  <p>Proin nulla arcu nonummy luctus dictum eget fermentum lorem</p>
</article>
<article class="service" style="left:246px">
  <div class="service-img" role="img" aria-label="Hands typing on a keyboard with code overlay" style="background:linear-gradient(135deg,#0d2230,#2b5a70 55%,#1a2c38)"></div>
  <h3>Threat Avoidance Plan<br>&amp; Dossier Creation</h3>
  <p>Proin nulla arcu nonummy luctu</p>
</article>
<article class="service" style="left:418px">
  <div class="service-img" role="img" aria-label="Security officer assisting travellers at a checkpoint" style="background:linear-gradient(135deg,#c9ccd2,#8a94a6 55%,#e2e4e8)"></div>
  <h3 style="margin-top:6px">Elite Executive Protection</h3>
  <p>Proin nulla arcu nonummy luctus dictum eget fermentum lorem</p>
</article>

<div class="divider"></div>

<section class="welcome">
  <h1>Welcome to Our Website Mainpage</h1>
  <p class="lead">Verdanith is a United States-based tier one security firm specializing in the protection of financial services professionals, executives and their families. We manage engagements resulting from general and specific threats throughout the United States and abroad on behalf of our domestic clients.</p>
  <p>We deliver our services exclusively through associates and contractors with United States special operations, secret service, CIA, or equivalent experience and training. We are one of only a handful of domestic security firms that offers scalable, tier one security services in every market in the United States.</p>
  <p>If you have a general or specific threat you would like to have assessed, it will be our privilege to evaluate your circumstances and provide you with an opinion of how to best address your security needs. Not all security circumstances require tier one professionals. It will be our pleasure to direct you to other firms in your market if you or we believe our service levels are not warranted.</p>
  <p class="gap">Our firm was created as the result of a specific threat to two of our founders resulting from a private equity transaction with a hostile seller. If you are a transaction professional or executive who is experiencing the fear and uncertainty of the risks associated with a general or specific security threat, it will be our privilege to help you manage this challenging process.</p>
</section>

<aside class="consult">
  <div class="consult-head">Request for Consulation</div>
  <div class="field" style="top:57px">First Name</div>
  <div class="field" style="top:89px">Last Name</div>
  <div class="field" style="top:122px">Home Phone</div>
  <div class="field" style="top:154px">Work Phone</div>
  <div class="field" style="top:187px">Cell Phone</div>
  <div class="field" style="top:219px">Email Address</div>
  <div class="field" style="top:252px">Address 1</div>
  <div class="field" style="top:284px">Address 2</div>
  <div class="field" style="top:317px">City</div>
  <div class="field" style="top:349px">State</div>
  <div class="field" style="top:382px">Zip</div>
  <div class="field message" style="top:415px">Message</div>
  <div class="submit">SUBMIT</div>
</aside>

<footer class="site-footer">
  <div class="footer-nav">Home<span class="sep">|</span>About Us<span class="sep">|</span>Our Services<span class="sep">|</span>Security<span class="sep">|</span>Testimonials<span class="sep">|</span>Team<span class="sep">|</span>Support<span class="sep">|</span>Contact Us</div>
  <div class="copyright">© 2014 &nbsp;Verdanith Inc. &nbsp;All right reserved. &nbsp;Term of Use</div>
  <div class="social">
    <span style="background:#3b5a98"></span>
    <span style="background:#4cb2e6"></span>
    <span style="background:#1e6fa8"></span>
  </div>
</footer>

</body>
</html>
```